Corporate Dinner Invite at Corvessa for BRQ

BRQ is hosting a corporate dinner at the VEP Summit and we need an email attachment invite for the event. Please use some images from this site for inspiration: https://www.corvessadining.example/ivyparlor/

Invite Title:
Join us for dinner!

Event Details:
Tuesday, October 24th 2023 at 6:30pm
Corvessa Dining, Ivy Parlor
347 W Marlow Ave, Chicago, IL 60622

Target Market(s)

Corporate Audience

Font styles to use
Script

Colors
0054AA
0677BA
7BADD7
CADEEF
E8F1F8

Requirements
Must have
• BRQ logo, event date / time, event location details, photo(s) from Ivy Parlor

```html
<!DOCTYPE html>
<html lang="en">
<head>
<meta charset="utf-8">
<title>BRQ Dinner Invitation – VEP Summit</title>
<link rel="stylesheet" href="https://fonts.googleapis.com/css2?family=Cormorant+Garamond:ital,wght@1,500;1,600&family=Damion&family=Montserrat:wght@700&family=Yellowtail&display=block">
<style>
  :root {
    --royal: #0a12d6;
    --royal-deep: #0008c8;
    --cyan: #1ae8f2;
    --gold: #e2b23f;
    --silver-light: #f1f3f3;
    --silver-mid: #c9d0d0;
    --silver-dark: #a9b3b3;
    --paper: #ffffff;
    --brand: #0054aa;
    --script: "Yellowtail", "Damion", cursive;
    --serif-italic: "Cormorant Garamond", serif;
  }
  * { box-sizing: border-box; margin: 0; padding: 0; }
  html, body { width: 915px; height: 1200px; overflow: hidden; }
  body { background: var(--paper); }

  .invite {
    position: relative;
    width: 915px;
    height: 1200px;
    overflow: hidden;
    background:
      radial-gradient(ellipse 120px 60px at 50% 0%, var(--cyan), transparent 100%),
      radial-gradient(ellipse 120px 60px at 50% 100%, var(--cyan), transparent 100%),
      var(--royal-deep);
  }
  .frame {
    position: absolute;
    left: 39px; top: 50px;
    width: 837px; height: 1099px;
    background: linear-gradient(90deg, var(--silver-dark), var(--silver-light) 30%, var(--silver-mid) 55%, var(--silver-light) 75%, var(--silver-dark));
  }
  .card {
    position: absolute;
    left: 64px; top: 76px;
    width: 787px; height: 1048px;
    background: var(--paper);
  }

  .brand {
    position: absolute;
    left: 0; right: 0; top: 172px;
    display: flex; justify-content: center; align-items: center; gap: 14px;
  }
  .brand-mark { width: 44px; height: 44px; background: var(--brand); }
  .brand-name {
    font-family: "Montserrat", sans-serif;
    font-weight: 700;
    font-size: 52px;
    letter-spacing: 2px;
    color: var(--brand);
    line-height: 1;
  }

  .headline { font-weight: 400; }
  .title-main {
    position: absolute;
    left: 168px; top: 300px;
    font-family: var(--script);
    font-weight: 400;
    font-size: 230px;
    color: var(--royal);
    line-height: 1;
    white-space: nowrap;
    text-shadow: 4px 4px 0 var(--cyan);
  }
  .title-lead {
    position: absolute;
    left: 496px; top: 318px;
    font-family: var(--script);
    font-weight: 400;
    font-size: 60px;
    color: var(--gold);
    line-height: 1;
    white-space: nowrap;
    transform: rotate(-4deg);
    transform-origin: left bottom;
  }

  .gallery { position: absolute; left: 0; top: 0; }
  .photo {
    position: absolute;
    border: 3px solid var(--paper);
    box-shadow: 0 3px 8px rgba(0,0,0,.25);
  }
  .photo-drinks {
    left: 150px; top: 585px; width: 225px; height: 150px;
    transform: rotate(16deg);
    background: linear-gradient(180deg, #3a2014, #1a0e08 55%, #d9d4cc 85%);
  }
  .photo-dining {
    left: 345px; top: 585px; width: 220px; height: 148px;
    transform: rotate(16deg);
    background: linear-gradient(160deg, #6b4020, #2a170c 50%, #c9b9a0);
  }
  .photo-bar {
    left: 510px; top: 588px; width: 245px; height: 150px;
    transform: rotate(20deg);
    background: linear-gradient(150deg, #2a1a10, #8a5a28 45%, #1c120b);
  }

  .venue-tag {
    position: absolute;
    left: 0; right: 0; top: 772px;
    text-align: center;
    font-family: var(--serif-italic);
    font-style: italic;
    font-weight: 500;
    font-size: 40px;
    line-height: 1.1;
    color: var(--cyan);
  }
  .venue-tag small { font-size: 20px; }

  .details {
    position: absolute;
    left: 232px; top: 830px;
    list-style: none;
    font-family: var(--serif-italic);
    font-style: italic;
    font-weight: 600;
    font-variant-numeric: lining-nums;
    color: var(--royal);
    white-space: nowrap;
  }
  .details li { display: flex; align-items: flex-start; gap: 14px; }
  .details .icon { width: 30px; height: 30px; flex: none; margin-top: 8px; }
  .detail-date, .detail-time { font-size: 38px; line-height: 44px; height: 42px; }
  .detail-place { font-size: 31px; line-height: 34px; margin-top: 2px; }

  .signoff {
    position: absolute;
    left: 0; right: 0; top: 1004px;
    text-align: center;
    font-family: var(--script);
    font-weight: 400;
    font-size: 72px;
    color: var(--royal);
    line-height: 1;
  }
</style>
</head>
<body>
<main class="invite">
  <div class="frame"></div>
  <div class="card"></div>

  <div class="brand">
    <span class="brand-mark"></span>
    <span class="brand-name">BRQ</span>
  </div>

  <h1 class="headline">
    <span class="title-main">Dinner</span>
    <span class="title-lead">Join us for</span>
  </h1>

  <div class="gallery">
    <div class="photo photo-drinks" role="img" aria-label="Cocktails lined up on a marble bar at Ivy Parlor"></div>
    <div class="photo photo-dining" role="img" aria-label="Candlelit dining room with arched mirrors at Ivy Parlor"></div>
    <div class="photo photo-bar" role="img" aria-label="Warmly lit bar and lounge seating at Ivy Parlor"></div>
  </div>

  <p class="venue-tag"><small>@</small> VEP Summit</p>

  <ul class="details">
    <li class="detail-date">
      <svg class="icon" viewBox="0 0 30 30" aria-hidden="true">
        <rect x="2" y="5" width="26" height="23" fill="var(--gold)"/>
        <rect x="7" y="2" width="3" height="6" fill="var(--gold)"/>
        <rect x="20" y="2" width="3" height="6" fill="var(--gold)"/>
        <g fill="#fff">
          <rect x="5" y="12" width="4" height="3"/><rect x="11" y="12" width="4" height="3"/><rect x="17" y="12" width="4" height="3"/><rect x="23" y="12" width="3" height="3"/>
          <rect x="5" y="17" width="4" height="3"/><rect x="11" y="17" width="4" height="3"/><rect x="17" y="17" width="4" height="3"/><rect x="23" y="17" width="3" height="3"/>
          <rect x="5" y="22" width="4" height="3"/><rect x="11" y="22" width="4" height="3"/><rect x="17" y="22" width="4" height="3"/>
        </g>
      </svg>
      <span>Tuesday, October 24th, 2023</span>
    </li>
    <li class="detail-time">
      <svg class="icon" viewBox="0 0 30 30" aria-hidden="true">
        <circle cx="15" cy="15" r="12.5" fill="none" stroke="var(--gold)" stroke-width="2.5"/>
        <path d="M15 8v8l5 4" fill="none" stroke="var(--gold)" stroke-width="2.5" stroke-linecap="round"/>
      </svg>
      <span>6:30pm</span>
    </li>
    <li class="detail-place">
      <svg class="icon" viewBox="0 0 30 30" aria-hidden="true">
        <circle cx="15" cy="15" r="12.5" fill="none" stroke="var(--gold)" stroke-width="2.5"/>
        <path d="M15 22c-3-4-5-6.5-5-9a5 5 0 0 1 10 0c0 2.5-2 5-5 9z" fill="none" stroke="var(--gold)" stroke-width="2"/>
        <circle cx="15" cy="13" r="1.8" fill="var(--gold)"/>
      </svg>
      <span>Corvessa Dining, Ivy Parlor<br>347 W Marlow Ave, Chicago, IL 60622</span>
    </li>
  </ul>

  <p class="signoff">See You There!</p>
</main>
</body>
</html>
```